Heron Loan Partners Business Card

We need a business card design for our mortgage servicing company. In addition to servicing the loans of homeowners, we help homeowners with purchasing their homes and any mortgage refinancing. We would like to see designs that use the colors in the logo attached below (gold-ish yellow and navy blue), and any other design you deem fit! The design should communicate a simpler life with smart mortgages provided by Heron.

```html
<!DOCTYPE html>
<html lang="en">
<head>
<meta charset="utf-8">
<title>Heron Loan Partners Business Card</title>
<link href="https://fonts.googleapis.com/css2?family=Arimo:wght@400;700&display=swap" rel="stylesheet">
<style>
  :root {
    --navy: #221f56;
    --gold: #dcae3a;
    --white: #ffffff;
    --ink: #3c3c44;
    --muted: #8a8a92;
    --rule: #d4d4d8;
    --stage: #3d3d3f;
  }
  * { margin: 0; padding: 0; box-sizing: border-box; }
  html, body { width: 1200px; height: 689px; overflow: hidden; }
  body {
    background: var(--stage);
    font-family: "Arimo", Arial, sans-serif;
    display: flex;
    align-items: center;
    justify-content: center;
    gap: 48px;
  }
  .card {
    position: relative;
    width: 520px;
    height: 300px;
    border-radius: 16px;
    overflow: hidden;
    box-shadow: 0 18px 40px rgba(0,0,0,0.45);
  }
  /* Back side */
  .card-back { background: var(--navy); }
  .card-back .brand {
    position: absolute;
    left: 0; right: 0; top: 104px;
    text-align: center;
    color: var(--gold);
    font-weight: 700;
    font-size: 38px;
    letter-spacing: 0.5px;
  }
  .card-back .tagline {
    position: absolute;
    left: 0; right: 0; top: 196px;
    text-align: center;
    color: var(--white);
    font-size: 15px;
    letter-spacing: 0.3px;
  }
  /* Front side */
  .card-front { background: var(--white); }
  .card-front .brand {
    position: absolute;
    right: 40px; top: 42px;
    color: var(--gold);
    font-weight: 700;
    font-size: 26px;
  }
  .card-front .top-rule {
    position: absolute;
    left: 200px; right: 40px; top: 96px;
    height: 1px;
    background: var(--rule);
  }
  .address {
    position: absolute;
    right: 40px; top: 108px;
    text-align: right;
    font-size: 12.5px;
    line-height: 1.45;
    color: var(--ink);
  }
  .person { position: absolute; left: 34px; top: 172px; }
  .person .name {
    color: var(--navy);
    font-weight: 700;
    font-size: 22px;
  }
  .person .role {
    color: var(--muted);
    font-size: 12.5px;
    margin-top: 2px;
  }
  .person .name-rule {
    width: 250px;
    height: 1px;
    background: var(--rule);
    margin: 8px 0 7px;
  }
  .contacts { list-style: none; }
  .contacts li {
    display: flex;
    align-items: center;
    gap: 9px;
    font-size: 12.5px;
    color: var(--ink);
    line-height: 1.5;
  }
  .contacts svg { width: 12px; height: 12px; fill: var(--gold); flex: none; }
  .band-navy, .band-gold { position: absolute; bottom: 0; height: 10px; }
  .band-navy { left: 0; width: 74%; background: var(--navy); }
  .band-gold { right: 0; width: 26%; background: var(--gold); }
</style>
</head>
<body>
  <section class="card card-back" aria-label="Card back">
    <div class="brand">Heron Loan Partners</div>
    <p class="tagline">Simpler life with smart mortgages</p>
  </section>

  <section class="card card-front" aria-label="Card front">
    <div class="brand">Heron Loan Partners</div>
    <div class="top-rule"></div>
    <address class="address" style="font-style:normal">
      4120 Willow Crest Road<br>
      Halifax, Canada 58213<br>
      www.heronloans.com
    </address>

    <div class="person">
      <h1 class="name">Daniel Reyes</h1>
      <p class="role">President</p>
      <div class="name-rule"></div>
      <ul class="contacts">
        <li>
          <svg viewBox="0 0 24 24" aria-hidden="true"><path d="M6.6 10.8a15.1 15.1 0 0 0 6.6 6.6l2.2-2.2a1 1 0 0 1 1-.25 11.4 11.4 0 0 0 3.6.57 1 1 0 0 1 1 1V20a1 1 0 0 1-1 1A17 17 0 0 1 3 4a1 1 0 0 1 1-1h3.5a1 1 0 0 1 1 1c0 1.25.2 2.45.57 3.57a1 1 0 0 1-.25 1z"/></svg>
          555-210-4387
        </li>
        <li>
          <svg viewBox="0 0 24 24" aria-hidden="true"><path d="M7 1h10a2 2 0 0 1 2 2v18a2 2 0 0 1-2 2H7a2 2 0 0 1-2-2V3a2 2 0 0 1 2-2zm0 3v14h10V4zm5 15.2a1.2 1.2 0 1 0 0 2.4 1.2 1.2 0 0 0 0-2.4z"/></svg>
          555-318-7290
        </li>
        <li>
          <svg viewBox="0 0 24 24" aria-hidden="true"><path d="M2 5h20v14H2zm2 2v.5l8 5 8-5V7zm0 2.8V17h16V9.8l-8 5z"/></svg>
          info@heronloans.com
        </li>
      </ul>
    </div>

    <div class="band-navy"></div>
    <div class="band-gold"></div>
  </section>
</body>
</html>
```